Homemaking training schools needs a Business Card design

Designer, Hello!

No special requirements, good-looking enough.
--------------------------------------------------------------------------

Name: Marcus Dole
Chairman
Tel: 0574-71948263
Mobile: 13857420916
Email: kelvora@mailnest.example
Web: www.prt2019.example
Add: No.258, LanpingJie, BeiyuanQu, Ningbo, Zhejiang

LOGO
Ningbo PRT Homemaking Training School

Target Market(s)

pregnant women, mothers, infants, the elderly and families, including cleaning, cooking, nursing training.

Industry/Entity Type

Business

Contact Information for Business Card

Name: Marcus Dole
Chairman
Tel: 0574-71948263
Mobile: 13857420916
Email: kelvora@mailnest.example
Web: www.prt2019.example

LOGO

Font styles to use
Serif
Sans Serif
Decorative

Requirements
Nice to have
• Feels: clean, specifications, safety, comfort, warmth and happiness.

```html
<!DOCTYPE html>
<html lang="en">
<head>
<meta charset="utf-8">
<title>PinRuiTang Business Card</title>
<link href="https://fonts.googleapis.com/css2?family=Nunito:wght@700&family=Open+Sans:wght@400;600&display=swap" rel="stylesheet">
<style>
  :root {
    --backdrop: #161616;
    --card-light: #f3f3f3;
    --card-blue: #1b73bb;
    --brand-blue: #1a6fb5;
    --accent-pink: #e6197f;
    --ink: #1d1d1d;
    --white: #ffffff;
  }
  * { margin: 0; padding: 0; box-sizing: border-box; }
  html, body { width: 1200px; height: 900px; overflow: hidden; }
  body {
    background: var(--backdrop);
    position: relative;
    font-family: "Open Sans", Arial, sans-serif;
  }
  .card {
    position: absolute;
    top: 184px;
    height: 491px;
    border-radius: 12px;
    text-align: center;
  }
  .card--front { left: 299px; width: 301px; background: var(--card-light); color: var(--ink); }
  .card--back { left: 645px; width: 305px; background: var(--card-blue); color: var(--white); }

  .brand { position: absolute; left: 0; right: 0; }
  .brand__dot { display: block; border-radius: 50%; margin: 0 auto; }
  .brand__name {
    display: block;
    font-family: "Nunito", Arial, sans-serif;
    font-weight: 700;
    letter-spacing: -0.5px;
    line-height: 1;
  }
  .card--front .brand { top: 38px; }
  .card--front .brand__dot { width: 14px; height: 14px; background: var(--accent-pink); margin-bottom: 42px; }
  .card--front .brand__name { font-size: 32px; color: var(--brand-blue); }
  .card--back .brand { top: 186px; }
  .card--back .brand__dot { width: 16px; height: 16px; background: var(--white); margin-bottom: 44px; }
  .card--back .brand__name { font-size: 38px; color: var(--white); }

  .holder { position: absolute; top: 265px; left: 0; right: 0; }
  .holder__name { font-size: 18px; font-weight: 600; color: var(--brand-blue); line-height: 22px; }
  .holder__title { font-size: 13.5px; line-height: 20px; }
  .address { position: absolute; top: 316px; left: 0; right: 0; font-size: 13.5px; line-height: 21px; }
  .contacts { position: absolute; top: 378px; left: 0; right: 0; list-style: none; font-size: 13px; line-height: 20.3px; }
  .contacts li { display: flex; justify-content: center; align-items: center; gap: 3px; }
  .contacts svg { width: 10px; height: 10px; fill: var(--brand-blue); }
</style>
</head>
<body>
  <section class="card card--front">
    <div class="brand">
      <span class="brand__dot"></span>
      <span class="brand__name">PinRuiTang</span>
    </div>
    <div class="holder">
      <p class="holder__name">Marcus Dole</p>
      <p class="holder__title">Chairman</p>
    </div>
    <p class="address">No.258, LanpingJie,<br>BeiyuanQu, Ningbo, Zhejiang</p>
    <ul class="contacts">
      <li><svg viewBox="0 0 10 10"><path d="M2 0.5 L3.6 2.6 L2.7 3.6 Q4 6 6.4 7.3 L7.4 6.4 L9.5 8 L8.3 9.5 Q2 8.5 0.5 1.7 Z"/></svg>0574-71948263</li>
      <li><svg viewBox="0 0 10 10"><path d="M3 0h4a1 1 0 0 1 1 1v8a1 1 0 0 1-1 1H3a1 1 0 0 1-1-1V1a1 1 0 0 1 1-1zm0.3 1.3v6.4h3.4V1.3z"/></svg>13857420916</li>
      <li><svg viewBox="0 0 10 10"><path d="M0 2h10v6H0z M0.6 2.4 5 5.6 9.4 2.4 9.4 3.2 5 6.4 0.6 3.2z" fill-rule="evenodd"/></svg>kelvora@mailnest.example</li>
      <li><svg viewBox="0 0 10 10"><circle cx="5" cy="5" r="5"/></svg>www.prt2019.example</li>
    </ul>
  </section>

  <section class="card card--back">
    <div class="brand">
      <span class="brand__dot"></span>
      <span class="brand__name">PinRuiTang</span>
    </div>
  </section>
</body>
</html>
```